New iOS App design for Boston Startup

We are looking for a new app design for our iPhone app. The current app's design feels outdated and we like to add lots of new functionality and a new navigation as well. A complete overhaul therefore!
We want you to design 5 screens that will have changed the most. The complete wireframes of these 5 pages are attached in the requirements document.
Once the winning design is selected we will award the winner with the designing all other screens (40-50 screens based on the same design). This will be a separate project worth $1000. The winning designer can get more follow up work if both sides are happy about the cooperation.
We will give feedback as soon as the first screen has been uploaded for review. Final decision will be made only after all 5 screens are finished.
We hope you give it your best!
Note: will only communicate through PixelHarbor (no skype),
Updates
Reason: Want to give designers a chance to submit their designs as I understand from some, the deadline is too close.
I have raised the award and introduced a 2nd price as well to make it worth your time. I hope you give it your best shot.
Reason: A few of you have asked for an extension of the deadline as time is running out. I will extend by one day. Tell me if you need more.
Industry/Entity Type
Startup
Requirements
Must have
- At least 1 screen before we can give you feedback.
Nice to have
- multiple options of 1 screen to get to a desirable design

```html
<!DOCTYPE html>
<html lang="en">
<head>
<meta charset="utf-8">
<title>Home Dashboard – Prep App</title>
<link rel="stylesheet" href="https://fonts.googleapis.com/css2?family=Open+Sans:wght@300;400;600;700&display=swap">
<style>
  :root {
    --brand-blue: #2a8fd6;
    --brand-blue-dark: #1f78b8;
    --ink-white: #ffffff;
    --ink-dark: #2b2b2b;
    --ink-muted: #8a8a8a;
    --gain-green: #a6e23a;
    --loss-red: #ff4b3a;
    --upnext-grey: #5f5f5f;
    --tab-bg: #f3f3f3;
    --tab-line: #dcdcdc;
    --page-bg: #ffffff;
  }
  * { box-sizing: border-box; margin: 0; padding: 0; }
  html, body {
    width: 1200px; height: 1041px; overflow: hidden;
    background: var(--page-bg);
    font-family: "Open Sans", Helvetica, Arial, sans-serif;
  }
  .screen {
    position: absolute; left: 390px; top: 148px;
    width: 420px; height: 746px;
    background: var(--page-bg);
    box-shadow: 0 0 0 1px #e6e6e6, 0 12px 40px rgba(0,0,0,.12);
    overflow: hidden;
  }
  /* ---------- header ---------- */
  .dashboard-header {
    position: absolute; left: 0; top: 0; width: 100%; height: 236px;
    background: var(--brand-blue); color: var(--ink-white);
  }
  .status-bar {
    position: absolute; left: 0; top: 0; width: 100%; height: 24px;
    display: flex; align-items: center; justify-content: space-between;
    padding: 0 10px; font-size: 11px; font-weight: 600;
  }
  .status-left, .status-right { display: flex; align-items: center; gap: 5px; width: 110px; }
  .status-right { justify-content: flex-end; }
  .battery { width: 24px; height: 11px; border: 1px solid #fff; border-radius: 2px; padding: 1px; }
  .battery span { display: block; width: 100%; height: 100%; background: #fff; }
  .title-bar {
    position: absolute; top: 26px; left: 0; width: 100%; height: 42px;
    display: flex; align-items: center; justify-content: center;
    font-size: 17px; font-weight: 600;
  }
  .menu-toggle { position: absolute; left: 14px; top: 11px; width: 24px; height: 20px; }
  .score-line {
    position: absolute; top: 70px; left: 0; width: 100%;
    display: flex; align-items: baseline; justify-content: center; gap: 12px;
  }
  .score-label { font-size: 32px; font-weight: 300; }
  .score-value { font-size: 66px; font-weight: 700; letter-spacing: -1px; }
  .score-delta { font-size: 24px; color: var(--loss-red); font-weight: 400; }
  .stats-row {
    position: absolute; top: 160px; left: 26px; right: 26px; height: 42px;
    display: flex; align-items: center; overflow: hidden; white-space: nowrap;
  }
  .stat { flex: 0 0 112px; text-align: center; border-right: 1px solid rgba(255,255,255,.55); }
  .stat:last-child { border-right: 0; }
  .stat-figures { font-size: 13px; font-weight: 600; }
  .stat-figures .value { color: var(--gain-green); }
  .stat-label { font-size: 11px; opacity: .9; }
  .stats-arrow { position: absolute; top: 172px; width: 10px; height: 16px; }
  .stats-arrow.prev { left: 8px; }
  .stats-arrow.next { right: 8px; }
  .pager { position: absolute; top: 214px; left: 0; width: 100%; display: flex; justify-content: center; gap: 7px; }
  .pager i { width: 7px; height: 7px; border-radius: 50%; border: 1px solid #fff; }
  .pager i.active { background: #fff; }
  /* ---------- body ---------- */
  .actions { position: absolute; top: 260px; left: 26px; right: 26px; display: flex; flex-direction: column; gap: 12px; }
  .action-button {
    height: 50px; border-radius: 4px; background: var(--brand-blue);
    color: var(--ink-white); font-size: 17px; font-weight: 400;
    display: flex; align-items: center; justify-content: center;
  }
  .up-next-label { position: absolute; top: 450px; width: 100%; text-align: center; font-size: 15px; color: var(--ink-dark); font-weight: 600; }
  .up-next-lesson {
    position: absolute; top: 478px; left: 26px; right: 26px; height: 50px;
    background: var(--upnext-grey); color: var(--ink-white); border-radius: 3px;
    display: flex; align-items: center; justify-content: center; font-size: 17px;
  }
  /* ---------- tab bar ---------- */
  .tab-bar {
    position: absolute; bottom: 0; left: 0; width: 100%; height: 64px;
    background: var(--tab-bg); border-top: 1px solid var(--tab-line);
    display: flex; justify-content: space-around; align-items: center;
  }
  .tab { display: flex; flex-direction: column; align-items: center; gap: 3px; font-size: 10px; font-weight: 600; color: var(--ink-muted); width: 70px; }
  .tab svg { width: 28px; height: 24px; }
  .tab.active { color: var(--ink-dark); }
</style>
</head>
<body>
<main class="screen">
  <header class="dashboard-header">
    <div class="status-bar">
      <div class="status-left">
        <span>VELA</span>
        <svg width="13" height="10" viewBox="0 0 13 10"><path d="M6.5 9.5 L1 3.5 A8 8 0 0 1 12 3.5 Z" fill="#fff"/></svg>
      </div>
      <span class="status-time">4:21 PM</span>
      <div class="status-right">
        <svg width="7" height="11" viewBox="0 0 7 11"><path d="M1 3 L6 8 L3.5 10.5 V0.5 L6 3 L1 8" fill="none" stroke="#fff" stroke-width="1"/></svg>
        <span>100%</span>
        <div class="battery"><span></span></div>
      </div>
    </div>
    <div class="title-bar">
      <svg class="menu-toggle" viewBox="0 0 24 20"><rect y="1" width="24" height="3" fill="#fff"/><rect y="8.5" width="24" height="3" fill="#fff"/><rect y="16" width="24" height="3" fill="#fff"/></svg>
      <h1 style="font-size:17px;font-weight:600">Welcome back, Noam</h1>
    </div>
    <div class="score-line">
      <span class="score-label">Score</span>
      <span class="score-value">650</span>
      <span class="score-delta">-18</span>
    </div>
    <svg class="stats-arrow prev" viewBox="0 0 10 16"><path d="M8 2 L2 8 L8 14" fill="none" stroke="#fff" stroke-width="2.4"/></svg>
    <div class="stats-row">
      <div class="stat"><div class="stat-figures"><span class="value">34%</span> +4</div><div class="stat-label">Completion</div></div>
      <div class="stat"><div class="stat-figures"><span class="value">20</span> +3</div><div class="stat-label">Sessions</div></div>
      <div class="stat"><div class="stat-figures"><span class="value">18</span> +10</div><div class="stat-label">Sessions</div></div>
      <div class="stat"><div class="stat-figures"><span class="value">5</span> +2</div><div class="stat-label">This week</div></div>
    </div>
    <svg class="stats-arrow next" viewBox="0 0 10 16"><path d="M2 2 L8 8 L2 14" fill="none" stroke="#fff" stroke-width="2.4"/></svg>
    <div class="pager"><i class="active"></i><i></i><i></i><i></i><i></i></div>
  </header>

  <nav class="actions">
    <div class="action-button">Analytics</div>
    <div class="action-button">Course Overview</div>
    <div class="action-button">Days Until test 33</div>
  </nav>

  <p class="up-next-label">Up Next:</p>
  <div class="up-next-lesson">Sentence Correction Lesson 4</div>

  <footer class="tab-bar">
    <div class="tab">
      <svg viewBox="0 0 28 24"><path d="M3 12 L14 3 L25 12 H21 V22 H16 V16 H12 V22 H7 V12 Z" fill="#8a8a8a"/></svg>
      Home
    </div>
    <div class="tab">
      <svg viewBox="0 0 28 24"><path d="M3 5 Q9 3 14 6 Q19 3 25 5 V21 Q19 19 14 22 Q9 19 3 21 Z M14 6 V22" fill="none" stroke="#8a8a8a" stroke-width="1.6"/></svg>
      Theory
    </div>
    <div class="tab active">
      <svg viewBox="0 0 28 24"><rect x="3" y="10" width="9" height="9" fill="#2a8fd6"/><rect x="10" y="6" width="9" height="9" fill="#2a8fd6"/><rect x="17" y="2" width="9" height="9" fill="#1f78b8"/></svg>
      Practice
    </div>
    <div class="tab">
      <svg viewBox="0 0 28 24"><path d="M7 7 H21 Q26 7 26 13 Q26 20 22 20 Q19 20 17 16 H11 Q9 20 6 20 Q2 20 2 13 Q2 7 7 7 Z" fill="#8a8a8a"/><rect x="6.5" y="11" width="5" height="1.6" fill="#f3f3f3"/><rect x="8.2" y="9.3" width="1.6" height="5" fill="#f3f3f3"/><circle cx="19" cy="11" r="1.2" fill="#f3f3f3"/><circle cx="21" cy="13.5" r="1.2" fill="#f3f3f3"/></svg>
      Games
    </div>
    <div class="tab">
      <svg viewBox="0 0 28 24"><circle cx="14" cy="12" r="10" fill="#8a8a8a"/><path d="M8.5 12 L12.5 16 L19.5 8.5" fill="none" stroke="#f3f3f3" stroke-width="2.6"/></svg>
      Test
    </div>
  </footer>
</main>
</body>
</html>
```